TALMORK

The business want a professional looking business card. We have a scetch we will add but want the extra upgrade, and would like more suggestions for variations of our business cards.

```html
<!DOCTYPE html>
<html lang="en">
<head>
<meta charset="utf-8">
<title>TALMORK Business Card</title>
<link href="https://fonts.googleapis.com/css2?family=Montserrat:wght@400;500;700&display=swap" rel="stylesheet">
<style>
  :root {
    --bg: #b9b9b9;
    --card: #1e1e1e;
    --card-deep: #161616;
    --gold: #d9ad4f;
    --gold-light: #f0cf7a;
    --gold-dark: #a67a26;
    --ink: #f2f2f2;
  }
  * { margin: 0; padding: 0; box-sizing: border-box; }
  html, body {
    width: 1200px; height: 802px; overflow: hidden;
    background: linear-gradient(180deg, #cfcfcf 0%, var(--bg) 100%);
    font-family: "Montserrat", sans-serif;
  }
  .stage {
    width: 1200px; height: 802px;
    display: flex; align-items: center; justify-content: center; gap: 40px;
  }
  .card {
    position: relative;
    width: 540px; height: 309px;
    background: var(--card);
    border-radius: 22px;
    border-bottom: 4px solid var(--gold);
    box-shadow: 0 0 0 1px var(--gold-dark), 0 14px 30px rgba(0,0,0,.35);
    overflow: hidden;
  }
  .wordmark {
    display: flex; flex-direction: column; align-items: center;
    color: var(--gold);
  }
  .wordmark__name {
    font-weight: 500; font-size: 30px; letter-spacing: 6px;
  }
  .wordmark__dot {
    width: 14px; height: 14px; border-radius: 50%;
    background: var(--gold); margin-bottom: 14px;
  }
  .wordmark__since {
    font-weight: 500; font-size: 9px; letter-spacing: 5px;
    margin-top: 6px;
  }
  /* Front */
  .card--front .brand {
    position: absolute; left: 0; top: 0; width: 250px; height: 100%;
    display: flex; align-items: center; justify-content: center;
  }
  .divider {
    position: absolute; left: 250px; top: 60px; width: 1px; height: 190px;
    background: linear-gradient(180deg, transparent, var(--gold-dark) 30%, var(--gold-dark) 70%, transparent);
  }
  .details {
    position: absolute; left: 280px; top: 66px; right: 20px;
    color: var(--ink);
  }
  .details__name {
    color: var(--gold); font-weight: 700; font-size: 20px; line-height: 1.1;
  }
  .details__role {
    font-size: 13px; margin-top: 4px;
  }
  .contacts { list-style: none; margin-top: 30px; }
  .contacts li {
    display: flex; align-items: center; gap: 10px;
    font-size: 13px; margin-bottom: 9px;
  }
  .contacts svg { width: 13px; height: 13px; flex: none; }
  /* Back */
  .card--back .pattern {
    position: absolute; inset: 0;
    background: linear-gradient(120deg, var(--card-deep) 0%, #262626 55%, #4a4a4a 100%);
  }
  .card--back .brand {
    position: absolute; right: 50px; top: 0; height: 100%;
    display: flex; align-items: center;
  }
</style>
</head>
<body>
<main class="stage">
  <section class="card card--front" aria-label="Business card front">
    <div class="brand">
      <div class="wordmark">
        <span class="wordmark__dot"></span>
        <span class="wordmark__name">TALMORK</span>
        <span class="wordmark__since">SINCE 2026</span>
      </div>
    </div>
    <div class="divider"></div>
    <div class="details">
      <h1 class="details__name">Eirik Halvor Moen</h1>
      <p class="details__role">CEO &amp; Founder</p>
      <ul class="contacts">
        <li>
          <svg viewBox="0 0 24 24" fill="var(--gold)"><path d="M6.6 10.8a15 15 0 0 0 6.6 6.6l2.2-2.2a1 1 0 0 1 1-.25 11.4 11.4 0 0 0 3.6.6 1 1 0 0 1 1 1V20a1 1 0 0 1-1 1A17 17 0 0 1 3 4a1 1 0 0 1 1-1h3.5a1 1 0 0 1 1 1c0 1.25.2 2.45.6 3.6a1 1 0 0 1-.25 1z"/></svg>
          004795550142
        </li>
        <li>
          <svg viewBox="0 0 24 24" fill="var(--gold)"><path d="M2 5h20v14H2z" fill="none" stroke="var(--gold)" stroke-width="2"/><path d="M2 5l10 8 10-8" fill="none" stroke="var(--gold)" stroke-width="2"/></svg>
          talmork.llc@postmail.com
        </li>
        <li>
          <svg viewBox="0 0 24 24" fill="none" stroke="var(--gold)" stroke-width="2"><circle cx="12" cy="12" r="9"/><path d="M3 12h18M12 3c3 3 3 15 0 18M12 3c-3 3-3 15 0 18"/></svg>
          www.talmork.llc
        </li>
      </ul>
    </div>
  </section>

  <section class="card card--back" aria-label="Business card back">
    <div class="pattern" role="img" aria-label="Repeating decorative floral pattern in dark grey tones"></div>
    <div class="brand">
      <div class="wordmark">
        <span class="wordmark__dot"></span>
        <span class="wordmark__name">TALMORK</span>
        <span class="wordmark__since">SINCE 2026</span>
      </div>
    </div>
  </section>
</main>
</body>
</html>
```